Cloud-based vaccination website

Basic website design for cloud-based medical company

Coding

Coded - Design and coding required

Number of Pages Required

1 page

Colors
3277b5

```html
<!DOCTYPE html>
<html lang="en">
<head>
<meta charset="utf-8">
<title>Velmora – Cloud Based Medical Company</title>
<link rel="stylesheet" href="https://fonts.googleapis.com/css2?family=Cinzel:wght@700&family=Open+Sans:wght@300;400;600;700&display=swap">
<style>
:root{
  --navy:#0c1f4f;
  --navy-dark:#0a1a44;
  --sky:#189ed3;
  --footer:#16305f;
  --grey-bg:#f2f2f2;
  --light-bg:#f6f6f6;
  --text:#444a55;
  --muted:#5b6270;
  --white:#ffffff;
  --border:#cfd3d8;
}
*{margin:0;padding:0;box-sizing:border-box}
html,body{width:1200px;height:3241px;overflow:hidden}
body{font-family:"Open Sans",Arial,sans-serif;color:var(--text);background:var(--white);position:relative}
section,header,footer{position:absolute;left:0;width:1200px}
.abs{position:absolute}
.heading{font-family:"Cinzel",Georgia,serif;font-weight:700;color:var(--navy);letter-spacing:.5px}
.btn{position:absolute;display:flex;align-items:center;justify-content:center;background:var(--navy);color:var(--white);font-weight:700;font-size:15px;border-radius:26px;text-transform:uppercase}

/* header */
.site-header{top:0;height:121px;background:var(--white)}
.brand{left:111px;top:38px}
.brand-name{font-size:40px;font-weight:700;color:var(--navy);line-height:1;display:flex;align-items:center;gap:10px}
.brand-dot{width:14px;height:14px;border-radius:50%;background:var(--sky)}
.brand-tag{font-size:10.5px;font-weight:600;color:var(--navy);margin-top:4px}
.main-nav{right:110px;top:54px;display:flex;gap:34px;font-size:12.5px;color:#333;text-transform:uppercase}
.main-nav .active{font-weight:700;color:var(--navy);position:relative}
.main-nav .active::after{content:"";position:absolute;left:-5px;right:-5px;top:62px;height:3px;background:var(--navy)}

/* hero */
.hero{top:121px;height:674px;background:linear-gradient(100deg,#0c2238 0%,#173a52 45%,#5f6e7c 75%,#a9afb5 100%)}
.hero-title{top:190px;width:100%;text-align:center;font-size:52px;color:var(--white)}
.hero-sub{top:260px;width:100%;text-align:center;font-size:25px;font-weight:300;color:#e4ecf2}
.hero .btn{left:522px;top:317px;width:156px;height:49px;border:2px solid #2f5fa8}
.dots{top:633px;left:572px;display:flex;gap:9px}
.dots span{width:8px;height:8px;border-radius:50%;background:var(--white)}
.dots span.hollow{background:transparent;border:1.5px solid var(--white)}

/* welcome */
.welcome{top:795px;height:473px;background:var(--sky);color:var(--white)}
.welcome h2{left:111px;top:55px;font-size:37px;color:var(--white)}
.welcome .copy{left:111px;top:112px;width:484px;font-size:14.5px;line-height:25px}
.welcome .copy p+p{margin-top:12px}
.welcome .btn{left:112px;top:333px;width:171px;height:51px}
.welcome-photo{left:641px;top:70px;width:448px;height:325px;border:4px solid #8fd0ea;background:radial-gradient(circle at 40% 45%,#4fc3f3 0%,#1269a8 35%,#0a2a55 75%,#06162f 100%)}

/* services */
.services{top:1268px;height:595px;background:var(--grey-bg)}
.services h2{top:64px;width:100%;text-align:center;font-size:38px}
.service{top:154px;width:230px;text-align:center}
.service .icon{width:128px;height:128px;margin:0 auto;border:2.5px solid var(--navy);border-radius:50%;display:flex;align-items:center;justify-content:center}
.service h3{margin-top:16px;font-size:15.5px;font-weight:700;color:#2a2f38;text-transform:uppercase}
.service p{margin-top:8px;font-size:13px;line-height:21.5px;color:var(--muted)}
.service .outline{display:inline-flex;margin-top:17px;width:128px;height:41px;align-items:center;justify-content:center;border:2px solid var(--navy);border-radius:22px;font-size:13px;font-weight:600;color:var(--navy);text-transform:uppercase}
.arrow{top:210px}

/* about */
.about{top:1863px;height:502px;background:var(--white)}
.about-photo{left:112px;top:68px;width:441px;height:366px;border:7px solid #f1f1f1;box-shadow:0 0 0 1px #e1e1e1;background:linear-gradient(90deg,#e6e9ec 0%,#f4f5f6 45%,#9ab7d6 80%,#5d84b4 100%)}
.about h2{left:598px;top:85px;font-size:38px}
.about .copy{left:599px;top:142px;width:490px;font-size:16px;line-height:23px;color:var(--muted)}
.about .copy p+p{margin-top:10px}
.about .btn{left:599px;top:347px;width:152px;height:49px}

/* contact */
.contact{top:2365px;height:566px;background:var(--light-bg)}
.contact h2{top:52px;width:100%;text-align:center;font-size:38px}
.contact .lead{top:103px;width:100%;text-align:center;font-size:16px;color:var(--muted)}
.field{position:absolute;background:var(--white);border:1px solid var(--border);font-size:14px;color:#555;padding:10px 13px}
.contact .btn{left:112px;top:448px;width:152px;height:44px}
.map{left:633px;top:158px;width:454px;height:341px;border:4px solid var(--white);background:linear-gradient(135deg,#efe9dc 0%,#f4efe4 40%,#e9e3d4 70%,#dfe8ef 100%)}

/* footer */
.site-footer{top:2931px;height:310px;background:var(--footer);color:var(--white)}
.footer-brand{left:111px;top:74px}
.footer-brand .brand-name{font-size:58px;color:var(--white);gap:0}
.footer-brand .brand-tag{font-size:16px;color:var(--white);margin-top:4px;font-weight:400}
.social{left:112px;top:172px;display:flex;gap:6px}
.social span{width:36px;height:36px;border-radius:50%;background:var(--sky)}
.quick-title{left:516px;top:78px;font-family:"Cinzel",Georgia,serif;font-weight:700;font-size:15px}
.links{top:112px;font-size:13.5px;color:#c9d4e6;line-height:25.8px}
.copyright{top:265px;width:100%;text-align:center;font-size:12.5px;color:#d5deec}
</style>
</head>
<body>

<header class="site-header">
  <div class="abs brand">
    <div class="brand-name"><span class="brand-dot"></span>VELMORA</div>
    <div class="brand-tag">Modern Digital Software Solutions</div>
  </div>
  <nav class="abs main-nav">
    <span class="active">Home</span><span>About Us</span><span>Our Services</span><span>Feature</span><span>Patients and Visitors</span><span>Blog</span><span>Contact Us</span>
  </nav>
</header>

<section class="hero" role="img" aria-label="Doctor in white coat holding a tablet with a glowing network overlay">
  <h1 class="abs heading hero-title">CLOUD BASED MEDICAL COMPANY</h1>
  <p class="abs hero-sub">We are a Velmora Modern Digital Software Solutions</p>
  <span class="btn">Contact Us</span>
  <div class="abs dots"><span class="hollow"></span><span></span><span></span><span></span></div>
</section>

<section class="welcome">
  <h2 class="abs heading">WELCOME TO VELMORA</h2>
  <div class="abs copy">
    <p>Lorem ipsum dolor sit amet, consectetur adipiscing elit, sed do eiusmod tempor incididunt ut labore et dolore magna aliqua. Ut enim ad minim veniam, quis nostrud exercitation ullamco laboris nisi ut aliquip ex ea commodo consequat.</p>
    <p>Sed ut perspiciatis unde omnis iste natus error sit voluptatem accusantium doloremque laudantium, totam rem aperiam, eaque ipsa quae ab illo inventore veritatis et quasi architecto beatae vitae dicta sunt explicabo</p>
  </div>
  <span class="btn">Learn More</span>
  <div class="abs welcome-photo" role="img" aria-label="Hand touching a glowing cloud icon in a server room"></div>
</section>

<section class="services">
  <h2 class="abs heading">VELMORA SERVICES</h2>
  <svg class="abs arrow" style="left:46px" width="26" height="46" viewBox="0 0 26 46"><path d="M22 3 L4 23 L22 43" fill="none" stroke="#9a9ea5" stroke-width="4"/></svg>
  <svg class="abs arrow" style="left:1117px" width="26" height="46" viewBox="0 0 26 46"><path d="M4 3 L22 23 L4 43" fill="none" stroke="#9a9ea5" stroke-width="4"/></svg>

  <div class="abs service" style="left:104px">
    <div class="icon"><svg width="64" height="64" viewBox="0 0 64 64" fill="none" stroke="#0c1f4f" stroke-width="2.5" stroke-linecap="round" stroke-linejoin="round"><path d="M32 24c-3-6-11-5-11 1 0 5 11 11 11 11s11-6 11-11c0-6-8-7-11-1z"/><path d="M8 20v18l10 12v8M56 20v18L46 50v8"/><path d="M14 30l8 8v6M50 30l-8 8v6"/></svg></div>
    <h3>Occaecat Cupidatat</h3>
    <p>Temporibus autem quibusdam et aut officiis debitis aut rerum necessitatibus saepe eveniet ut et voluptates sint et molestiae non recusandae. Itaque earum rerum hic tenetur a sapiente reiciendis voluptatibus delectus.</p>
    <span class="outline">Learn More</span>
  </div>
  <div class="abs service" style="left:358px">
    <div class="icon"><svg width="64" height="64" viewBox="0 0 64 64" fill="none" stroke="#0c1f4f" stroke-width="2.5" stroke-linecap="round" stroke-linejoin="round"><path d="M40 14l10 10M45 19l8-8M36 18l10 10L24 50l-10-10z"/><path d="M14 40l-6 6 10 10 6-6M8 56l4-4"/><path d="M26 32l4 4M22 36l4 4"/></svg></div>
    <h3>Numquam Eius</h3>
    <p>Temporibus autem quibusdam et aut officiis debitis aut rerum necessitatibus saepe eveniet ut et voluptates sint et molestiae non recusandae. Itaque earum rerum hic tenetur a sapiente reiciendis voluptatibus delectus.</p>
    <span class="outline">Learn More</span>
  </div>
  <div class="abs service" style="left:612px">
    <div class="icon"><svg width="64" height="64" viewBox="0 0 64 64" fill="none" stroke="#0c1f4f" stroke-width="2.5" stroke-linecap="round" stroke-linejoin="round"><path d="M24 46c-6-3-10-9-10-16 0-10 8-18 18-18s18 8 18 18c0 7-4 13-10 16v6H24z"/><path d="M32 12v34M24 24h8M32 32h8M26 52h12M28 58h8"/></svg></div>
    <h3>Tempora Incidunt</h3>
    <p>Temporibus autem quibusdam et aut officiis debitis aut rerum necessitatibus saepe eveniet ut et voluptates sint et molestiae non recusandae. Itaque earum rerum hic tenetur a sapiente reiciendis voluptatibus delectus.</p>
    <span class="outline">Learn More</span>
  </div>
  <div class="abs service" style="left:866px">
    <div class="icon"><svg width="64" height="64" viewBox="0 0 64 64" fill="none" stroke="#0c1f4f" stroke-width="2.5" stroke-linecap="round" stroke-linejoin="round"><path d="M18 44h-2a10 10 0 0 1 0-20 14 14 0 0 1 27-4 11 11 0 0 1 6 24h-3"/><circle cx="32" cy="42" r="6"/><path d="M32 30v4M32 50v4M20 42h4M40 42h4M24 34l3 3M37 47l3 3M40 34l-3 3M27 47l-3 3"/></svg></div>
    <h3>Voluptate Velit</h3>
    <p>Temporibus autem quibusdam et aut officiis debitis aut rerum necessitatibus saepe eveniet ut et voluptates sint et molestiae non recusandae. Itaque earum rerum hic tenetur a sapiente reiciendis voluptatibus delectus.</p>
    <span class="outline">Learn More</span>
  </div>
</section>

<section class="about">
  <div class="abs about-photo" role="img" aria-label="Medical staff in white coats and scrubs standing with arms crossed"></div>
  <h2 class="abs heading">ABOUT VELMORA</h2>
  <div class="abs copy">
    <p>But I must explain to you how all this mistaken idea of denouncing pleasure and praising pain was born and I will give you a complete account of the system, and expound the actual teachings of the great explorer of the truth, the master-builder of human happiness.</p>
    <p>But who has any right to find fault with a man who chooses to enjoy a pleasure that has no annoying consequences, or one who avoids a pain that produces no resultant pleasure.</p>
  </div>
  <span class="btn">Learn More</span>
</section>

<section class="contact">
  <h2 class="abs heading">CONTACT US</h2>
  <p class="abs lead">Please use the contact form below to get in touch.</p>
  <div class="field" style="left:112px;top:171px;width:239px;height:39px">First name</div>
  <div class="field" style="left:361px;top:171px;width:239px;height:39px">Last name</div>
  <div class="field" style="left:112px;top:223px;width:488px;height:39px">Your email</div>
  <div class="field" style="left:112px;top:274px;width:488px;height:39px">Phone</div>
  <div class="field" style="left:112px;top:326px;width:488px;height:93px">Your message</div>
  <span class="btn">Submit Now</span>
  <div class="abs map" role="img" aria-label="Street map of the office location with route markers"></div>
</section>

<footer class="site-footer">
  <div class="abs footer-brand">
    <div class="brand-name">VELMORA</div>
    <div class="brand-tag">Modern Digital Software Solutions</div>
  </div>
  <div class="abs social" aria-label="Social links"><span></span><span></span><span></span></div>
  <h4 class="abs quick-title">QUICK LINKS</h4>
  <div class="abs links" style="left:516px">About Us<br>Vaccination Services<br>Blog<br>Contact</div>
  <div class="abs links" style="left:750px">Privacy Policy<br>Disclaimer<br>Terms of Use</div>
  <div class="abs links" style="left:959px">Medical Professionals<br>Online Appointments<br>Client Partners</div>
  <p class="abs copyright">Copyrights © 2021, VELMORA Modern Digital Software Solutions. All rights reserved.</p>
</footer>

</body>
</html>
```